Business cards and stationary design

We just completed the design of our new logo and we need to print new business cards and letterhead for our nonprofit. We are looking for a fresh new design that shows off our new logo. On letterhead, we must have a column on the right or left to include our Board of Directors (up to 45 names) (see attachment)

Industry/Entity Type

Non-Profit

Contact Information for Business Card

Standard business card with name, title, Company name, mailing address phone numbers, email address and website. Tagline on back "Bringing the homeless home"

Font styles to use
Sans Serif

Requirements
Must have
• include pertinent information above
• new logo
• fonts compatible with logo
• should use logo colors only
Nice to have
• tag lines

```html
<!DOCTYPE html>
<html lang="en">
<head>
<meta charset="utf-8">
<title>Shelter Bridge Center – Business Card</title>
<link rel="stylesheet" href="https://fonts.googleapis.com/css2?family=Roboto:wght@400;500&family=Roboto+Condensed:wght@500;700&display=swap">
<style>
  :root {
    --bg: #2b2b2b;
    --red: #d62027;
    --paper: #f1f1f1;
    --teal: #0b86a3;
    --teal-dark: #0e7f9b;
    --yellow: #f8bb22;
    --white: #ffffff;
  }
  html, body {
    margin: 0;
    padding: 0;
    width: 1200px;
    height: 960px;
    overflow: hidden;
    background: var(--bg);
    font-family: "Roboto", Arial, sans-serif;
  }
  .canvas {
    position: relative;
    width: 1200px;
    height: 960px;
  }
  .card {
    position: absolute;
    left: 320px;
    width: 600px;
    height: 342px;
    overflow: hidden;
  }
  /* front */
  .card-front {
    top: 103px;
    background: var(--red);
  }
  .front-brand {
    position: absolute;
    left: 0;
    right: 0;
    top: 150px;
    display: flex;
    justify-content: center;
    align-items: center;
    gap: 14px;
    color: var(--white);
    font-family: "Roboto Condensed", Arial, sans-serif;
    font-weight: 700;
    font-size: 34px;
    letter-spacing: 3px;
  }
  .front-brand .dot {
    width: 18px;
    height: 18px;
    border-radius: 50%;
    background: var(--white);
  }
  .front-web {
    position: absolute;
    left: 0;
    right: 0;
    top: 296px;
    text-align: center;
    color: var(--white);
    font-size: 14px;
    letter-spacing: 5px;
  }
  /* back */
  .card-back {
    top: 493px;
    background: var(--paper);
  }
  .back-brand {
    position: absolute;
    right: 30px;
    top: 110px;
    color: var(--teal);
    font-family: "Roboto Condensed", Arial, sans-serif;
    font-weight: 500;
    font-size: 23px;
    letter-spacing: 2px;
  }
  .name-band {
    position: absolute;
    left: 0;
    top: 173px;
    width: 290px;
    height: 67px;
  }
  .name-band svg { position: absolute; inset: 0; }
  .person {
    position: absolute;
    left: 33px;
    top: 186px;
    color: var(--white);
  }
  .person-name {
    font-family: "Roboto Condensed", Arial, sans-serif;
    font-weight: 700;
    font-size: 23px;
    line-height: 1;
  }
  .person-title {
    font-family: "Roboto Condensed", Arial, sans-serif;
    font-weight: 500;
    font-size: 15px;
    margin-top: 5px;
  }
  .info-band {
    position: absolute;
    left: 0;
    right: 0;
    top: 242px;
    height: 100px;
    background: var(--teal);
    color: var(--white);
    font-size: 14.5px;
  }
  .contacts {
    list-style: none;
    margin: 0;
    padding: 0;
    position: absolute;
    left: 33px;
    top: 21px;
  }
  .contacts li {
    display: flex;
    align-items: center;
    gap: 8px;
    height: 19px;
  }
  .contacts svg { width: 13px; height: 13px; flex: none; }
  .address {
    position: absolute;
    right: 24px;
    top: 24px;
    text-align: right;
    line-height: 18.5px;
  }
  .address .org { font-weight: 500; }
</style>
</head>
<body>
<div class="canvas">

  <section class="card card-front">
    <div class="front-brand"><span class="dot"></span>SHELTER BRIDGE CENTER</div>
    <div class="front-web">www.shelterbridge.com</div>
  </section>

  <section class="card card-back">
    <div class="back-brand">SHELTER BRIDGE CENTER</div>

    <div class="name-band">
      <svg width="290" height="67" viewBox="0 0 290 67">
        <polygon points="0,0 217,0 290,67 0,67" fill="var(--yellow)"/>
      </svg>
    </div>
    <div class="person">
      <div class="person-name">DANIEL REYES</div>
      <div class="person-title">CEO/FOUNDER</div>
    </div>

    <div class="info-band">
      <ul class="contacts">
        <li>
          <svg viewBox="0 0 16 16"><path fill="#fff" d="M3.5 1l2.5 3-1.5 2c1 2 2.5 3.5 4.5 4.5l2-1.5 3 2.5-1.5 2.5C6 14 2 10 1 2.5z"/></svg>
          555 214 7093
        </li>
        <li>
          <svg viewBox="0 0 16 16"><rect x="1" y="3" width="14" height="10" fill="#fff"/><path d="M1 3l7 6 7-6" fill="none" stroke="var(--teal)" stroke-width="1.4"/></svg>
          daniel@shelterbridge.com
        </li>
        <li>
          <svg viewBox="0 0 16 16"><circle cx="8" cy="8" r="7" fill="#fff"/><path d="M5 4c2 1 1 3 3 3s1 3 3 4M10 3c-1 1 0 2 1 2" fill="none" stroke="var(--teal)" stroke-width="1.4"/></svg>
          www.shelterbridge.com
        </li>
      </ul>
      <div class="address">
        <div class="org">Shelter bridge center</div>
        <div>2261 Maple Court</div>
        <div>Fairview, Alaska 34518</div>
      </div>
    </div>
  </section>

</div>
</body>
</html>
```